Flyer Design for Private Car Service

Flyer should cater to Business Travelers and Executives who travel Business Class or First Class.
Flyer should include images attached.
Flyer should include the below text
Dallas to Austin
Chauffeured SUVs
• Travel Dallas to Austin in a new 2025 Norvak Tressel for $499 one-way
• Trip includes a Uniformed Chauffeur who has a Commercial Drivers License (CDL)
• You can Schedule Chauffeur Pickup at Your Home in Dallas
• Our Chauffeur will Drop You Off at Your Final Destination in Austin
• You can Schedule Chauffeur Return Pickup in Austin and Return Back to Dallas.
• We offer Faster Times on Door-to-Door Travel than Bluequill Airways
• We offer Comparable Prices on Door-to-Door Travel Times than Bluequill Airways
• All of our trips are insured with $500k of commercial auto insurance
• Our Passengers can Talk on Cell Phone & Conduct Kavlo calls Throughout Travel
• Our Passengers have Maximum Privacy, Comfort and First-Class Amenities.
• Our Passengers Avoid Marrow Pike Airfield and QHN Airport hassles & delays
• Member Tellbrook Chamber of Commerce, Pindle Chamber of Commerce.
• Book your trip today at www.quorvanride.example
Target Market(s)
Business Travelers
Look and feel

```html
<!DOCTYPE html>
<html lang="en">
<head>
<meta charset="utf-8">
<title>Dallas to Austin Chauffeured SUVs</title>
<link rel="stylesheet" href="https://fonts.googleapis.com/css2?family=Prata&family=Poppins:wght@400;700&display=swap">
<style>
  :root {
    --ink: #1a1a1a;
    --black: #0d0d0d;
    --red: #ee2a30;
    --white: #ffffff;
    --photo-top: linear-gradient(180deg, #e7e3df 0%, #cfcac6 45%, #6d6c6c 75%, #b9b5b1 100%);
    --photo-side: linear-gradient(160deg, #cfd3d6 0%, #4b4a4c 45%, #1f1d1e 100%);
    --photo-crew: linear-gradient(135deg, #b8c0c8 0%, #3f5f8f 25%, #232323 60%, #141414 100%);
  }
  * { box-sizing: border-box; margin: 0; padding: 0; }
  html, body { width: 927px; height: 1200px; overflow: hidden; background: var(--white); }
  .flyer { position: relative; width: 927px; height: 1200px; overflow: hidden; background: var(--white); font-family: "Poppins", sans-serif; color: var(--ink); }
  .photo { position: absolute; }
  .photo-fleet { left: 0; top: 0; width: 927px; height: 430px; background: var(--photo-top); }
  .photo-greeting { left: 635px; top: 429px; width: 292px; height: 364px; background: var(--photo-side); border-top-left-radius: 70px; border-bottom-left-radius: 70px; outline: 5px solid var(--white); }
  .photo-crew { left: 0; top: 836px; width: 316px; height: 269px; background: var(--photo-crew); border-top-right-radius: 60px; border-bottom-right-radius: 60px; outline: 5px solid var(--white); }
  .shapes { position: absolute; left: 0; top: 0; width: 927px; height: 1200px; }
  .brand { position: absolute; left: 600px; top: 96px; width: 300px; text-align: center; font-family: "Prata", serif; color: var(--white); white-space: nowrap; line-height: 1; }
  .brand-name { display: block; font-size: 38px; letter-spacing: 1px; }
  .brand-sub { display: block; font-size: 22px; margin-top: 6px; letter-spacing: 1px; }
  .title { position: absolute; left: 22px; top: 398px; font-family: "Prata", serif; line-height: 1; font-weight: 400; }
  .title-main { color: var(--red); font-size: 51px; letter-spacing: 1px; }
  .title-sub { color: var(--white); font-size: 32px; margin-top: 8px; letter-spacing: 0.5px; }
  .features { list-style: none; position: absolute; font-size: 13px; line-height: 19.6px; letter-spacing: 0.3px; }
  .features li { position: relative; padding-left: 26px; margin-bottom: 15px; }
  .features li::before { content: ""; position: absolute; left: 2px; top: 5px; width: 10px; height: 10px; border-radius: 50%; background: var(--red); }
  .col-left { left: 23px; top: 590px; width: 280px; }
  .col-mid { left: 333px; top: 590px; width: 290px; }
  .col-wide { left: 333px; top: 811px; width: 590px; }
  .col-wide li { margin-bottom: 18px; }
  .cta { position: absolute; left: 0; top: 1122px; width: 927px; text-align: center; font-family: "Poppins", sans-serif; font-weight: 700; font-size: 31px; line-height: 1.2; color: var(--white); white-space: nowrap; }
  .cta-link { color: var(--red); }
</style>
</head>
<body>
<main class="flyer">
  <div class="photo photo-fleet" role="img" aria-label="Four uniformed chauffeurs standing beside black, white and red SUVs in front of an office building"></div>

  <svg class="shapes" viewBox="0 0 927 1200" aria-hidden="true">
    <path d="M432 0 Q500 150 690 196 Q820 218 927 188 L927 0 Z" fill="var(--red)"/>
    <path d="M446 0 Q520 140 700 186 Q820 206 927 176 L927 0 Z" fill="var(--white)"/>
    <path d="M458 0 Q530 132 704 178 Q820 198 927 168 L927 0 Z" fill="var(--black)"/>
    <line x1="606" y1="86" x2="894" y2="86" stroke="var(--red)" stroke-width="1.5"/>
    <path d="M0 393 L580 393 Q592 393 598 405 L629 512 Q300 498 0 540 Z" fill="#211f20"/>
    <path d="M0 540 Q300 498 629 512 L629 526 Q300 514 0 580 Z" fill="var(--red)"/>
    <path d="M316 1030 Q650 1010 927 1078 L927 1200 L0 1200 L0 1105 L316 1105 Z" fill="var(--red)"/>
    <path d="M316 1045 Q650 1030 927 1094 L927 1200 L0 1200 L0 1105 L316 1105 Z" fill="var(--black)"/>
  </svg>

  <div class="brand">
    <span class="brand-name">QUORVAN</span>
    <span class="brand-sub">RIDE</span>
  </div>

  <h1 class="title">
    <div class="title-main">DALLAS TO AUSTIN</div>
    <div class="title-sub">CHAUFFEURED SUVS</div>
  </h1>

  <div class="photo photo-greeting" role="img" aria-label="Chauffeur greeting a business traveler with luggage beside a black SUV"></div>

  <ul class="features col-left">
    <li>Travel Dallas to Austin in a new 2025 Norvak Tressel for $499 one-way</li>
    <li>Trip includes a Uniformed Chauffeur who has a Commercial Drivers License (CDL)</li>
    <li>You can Schedule Chauffeur Pickup at Your Home in Dallas</li>
    <li>Our Chauffeur will Drop You Off at Your Final Destination in Austin</li>
  </ul>

  <ul class="features col-mid">
    <li>You can Schedule Chauffeur Return Pickup in Austin and Return Back to Dallas</li>
    <li>We offer Faster Times on Door-to-Door Travel than Bluequill Airways</li>
    <li>We offer Comparable Prices on Door-to-Door Travel Times than Bluequill Airways</li>
  </ul>

  <ul class="features col-wide">
    <li>All of our trips are insured with $500k of commercial auto insurance</li>
    <li>Our Passengers can Talk on Cell Phone &amp; Conduct Kavlo calls Throughout Travel</li>
    <li>Our Passengers have Maximum Privacy, Comfort and First-Class Amenities</li>
    <li>Our Passengers Avoid Marrow Pike Airfield and QHN Airport hassles &amp; delays</li>
    <li>Member Tellbrook Chamber of Commerce, Pindle Chamber of Commerce.</li>
  </ul>

  <div class="photo photo-crew" role="img" aria-label="Row of uniformed chauffeurs in caps and black jackets"></div>

  <p class="cta">Book your trip today at <span class="cta-link">www.quorvanride.example</span></p>
</main>
</body>
</html>
```